Website for IT consulting Company

I need a website upgrade, the existing site content is ok, I would also like to add a testimonial page, the site should be something that is easy for us to update content. You use the content from www.kelvanbrook.com as an example. I will also post update logo and artwork. I also need a contact form with some type of validation or captcha.

I added Coded to the Project

Please omit Address maps

Target Market(s)

small business, service oriented companies. We provide IT Consulting, support and mangement

Industry/Entity Type

Information Technology

Coding

Number of Pages Required

1 page

Font styles to use
Serif
Sans Serif

Requirements
Must have
• Contain logo attached, and content from existing web site www.kelvanbrook.com.
• Also need to update content easily, and be movable to different platforms.
• There is a catch phrase
• "Let us worry about your technology…” “ so you don’t have to!”
• Should be included.
Nice to have
• Testimonial page, Project page where we can post new and past projects and pictures
Should not have
• none

```html
<!DOCTYPE html>
<html lang="en">
<head>
<meta charset="utf-8">
<title>Kelvanbrook – IT Solutions</title>
<link rel="stylesheet" href="https://fonts.googleapis.com/css2?family=Montserrat:wght@400;500;600;700&family=Open+Sans:wght@400;600&display=swap">
<style>
:root{
  --orange:#f08a24;
  --orange-dark:#e27512;
  --ink:#333333;
  --text:#555555;
  --grey-band:#ededed;
  --grey-line:#d9d9d9;
  --logo-grey:#8a8a8a;
  --white:#ffffff;
  --hero-dark:rgba(60,60,60,.82);
}
*{margin:0;padding:0;box-sizing:border-box}
html,body{width:1200px;height:3396px;overflow:hidden;background:var(--white)}
body{font-family:"Open Sans",Arial,sans-serif;color:var(--text);position:relative}
.section{position:absolute;left:0;width:1200px}
.abs{position:absolute}
.heading{font-family:"Montserrat",Arial,sans-serif;color:var(--orange);font-weight:600;text-transform:uppercase;letter-spacing:.5px}
.center{text-align:center}
.rule{width:80px;height:2px;background:var(--grey-line);position:absolute;left:560px}

/* Header */
.site-header{top:0;height:125px;background:var(--white)}
.brand{left:132px;top:24px;display:flex;align-items:center;gap:10px}
.brand-mark{width:40px;height:40px;background:var(--orange);border-radius:6px}
.brand-name{font-family:"Montserrat",Arial,sans-serif;font-weight:700;font-size:31px;color:var(--logo-grey);letter-spacing:.5px;line-height:1}
.brand-tagline{left:184px;top:70px;font-size:9px;color:var(--orange);font-style:italic;white-space:nowrap}
.callbar{left:668px;top:24px;display:flex;align-items:center;gap:10px;font-size:10px;color:var(--ink);text-transform:uppercase}
.round-icon{width:26px;height:26px;border-radius:50%;background:var(--orange);display:flex;align-items:center;justify-content:center}
.callbar .phone{font-size:19px;color:var(--orange);font-family:"Montserrat",sans-serif;margin-right:30px;text-transform:none}
.social{display:flex;gap:7px}
.social span{width:24px;height:24px;border-radius:50%;display:block}
.s1{background:#3b5998}.s2{background:#2fa7e0}.s3{background:#dd4b39}
.main-nav{left:516px;top:74px;display:flex;font-family:"Montserrat",sans-serif;font-size:11.5px;font-weight:500;color:var(--ink);text-transform:uppercase}
.main-nav a{padding:12px 11px;text-decoration:none;color:inherit}
.main-nav a.active{background:var(--orange);color:var(--white)}

/* Hero */
.hero{top:125px;height:538px;overflow:hidden}
.hero-photo{position:absolute;inset:0;background:linear-gradient(100deg,#cfd4d8 0%,#e9ecee 30%,#b9bfc4 55%,#dfe3e6 80%,#c8cdd1 100%)}
.hero-box{left:686px;top:120px;width:408px;height:250px;background:var(--hero-dark)}
.hero-title{position:absolute;left:0;right:0;top:28px;text-align:center;font-family:"Montserrat",sans-serif;font-weight:600;font-size:40px;line-height:52px;color:var(--white);text-transform:uppercase}
.hero-sub{position:absolute;left:0;right:0;bottom:0;height:44px;background:var(--orange);color:var(--white);text-align:center;line-height:44px;font-family:"Montserrat",sans-serif;font-size:17px;font-weight:500}
.dots{left:545px;top:483px;display:flex;gap:12px}
.dots span{width:10px;height:10px;border-radius:50%;background:rgba(255,255,255,.7)}
.dots span.on{background:var(--white);box-shadow:0 0 0 2px rgba(255,255,255,.5)}

/* Support */
.support{top:663px;height:333px;background:var(--grey-band)}
.support .heading{top:45px;width:100%;font-size:22px}
.support .rule{top:95px}
.support-item{top:142px;width:160px;text-align:center;font-size:15px;line-height:23px}
.support-item svg{display:block;margin:0 auto 20px}
.support-item .a{color:var(--orange)}
.support-item .b{color:var(--ink)}

/* Welcome */
.welcome{top:996px;height:449px;background:var(--white)}
.welcome .heading{top:52px;width:100%;font-size:22px}
.welcome .big-name{top:105px;width:100%;font-family:"Montserrat",sans-serif;font-weight:700;font-size:46px;color:var(--logo-grey);letter-spacing:1px}
.welcome p{left:300px;top:208px;width:600px;font-size:13.5px;line-height:27px;color:var(--ink)}
.btn{background:var(--orange);color:var(--white);font-family:"Montserrat",sans-serif;font-weight:600;text-transform:uppercase;text-align:center}
.welcome .btn{left:537px;top:349px;width:124px;height:38px;line-height:38px;font-size:13px}

/* Services */
.services{top:1445px;height:475px;background:repeating-linear-gradient(135deg,#eeeeee 0 3px,#e6e6e6 3px 5px)}
.service{top:50px;width:320px;text-align:center}
.service .ring{width:120px;height:120px;border-radius:50%;background:var(--white);margin:0 auto;display:flex;align-items:center;justify-content:center;box-shadow:0 2px 6px rgba(0,0,0,.12)}
.service .disc{width:100px;height:100px;border-radius:50%;background:var(--orange);display:flex;align-items:center;justify-content:center}
.service h3{margin-top:52px;font-family:"Montserrat",sans-serif;font-weight:600;font-size:16px;color:var(--orange);line-height:23px;text-transform:uppercase}
.service h3 span{font-weight:400}
.service p{margin:22px auto 0;width:240px;font-size:13px;line-height:21px;color:var(--ink)}

/* Flexible */
.flexible{top:1920px;height:521px;background:var(--white)}
.flexible h2{left:131px;top:70px;font-size:27px;line-height:46px;font-weight:600}
.flexible p{left:131px;top:200px;width:545px;font-size:13.5px;line-height:25px;color:var(--ink)}
.divider{left:754px;top:68px;width:1px;height:276px;background:var(--grey-line)}
.flex-mark{left:856px;top:72px;width:200px;height:200px}
.flex-mark .sq{position:absolute;left:30px;top:10px;width:140px;height:140px;background:linear-gradient(135deg,#f6a244,var(--orange-dark));border-radius:14px}
.feature{top:378px;width:226px;height:74px;border:1px solid var(--grey-line);box-shadow:0 1px 4px rgba(0,0,0,.1);display:flex;align-items:center;gap:10px;padding-left:14px;font-family:"Montserrat",sans-serif;font-size:11px;font-weight:500;color:var(--ink);text-transform:uppercase;white-space:nowrap}

/* Testimonials */
.testimonials{top:2441px;height:532px;background:var(--grey-band)}
.testimonials .heading{top:55px;width:100%;font-size:22px}
.testimonials .rule{top:102px}
.avatar{border-radius:50%;background:radial-gradient(circle at 50% 40%,#d8c3b0,#8d8f94 70%)}
.avatar.main{border:5px solid var(--white);box-shadow:0 2px 8px rgba(0,0,0,.2);background:radial-gradient(circle at 50% 40%,#7a5e4d,#2f3b4f 70%)}
.arrow{font-size:34px;color:#888;font-family:"Montserrat",sans-serif}
.quote-mark{font-family:Georgia,serif;font-size:110px;color:#cfcfcf;line-height:1}
.testimonials p{left:320px;top:320px;width:560px;text-align:center;font-size:13.5px;line-height:25px;color:var(--ink)}
.name-tag{left:514px;top:445px;width:174px;height:30px;line-height:30px;font-size:11px;text-transform:none}
.name-tag b{font-weight:700;text-transform:uppercase}
.name-tag span{font-weight:400}

/* Footer */
.site-footer{top:2973px;height:423px;background:var(--white)}
.site-footer .brand{left:132px;top:68px}
.site-footer .brand-tagline{left:184px;top:114px}
.connect{left:200px;top:188px;width:202px;font-size:13px}
.foot-social{left:248px;top:232px;display:flex;gap:9px}
.foot-social span{width:28px;height:28px;border-radius:50%}
.foot-title{font-size:13px}
.menu{left:577px;top:61px}
.menu ul{list-style:none;margin-top:25px}
.menu li{font-size:12.5px;line-height:25.6px;color:var(--ink)}
.contact{left:817px;top:61px}
.contact-row{position:absolute;left:0;display:flex;align-items:center;gap:16px;font-size:12.5px;line-height:20px;color:var(--ink);width:320px}
.contact-row .round-icon{width:28px;height:28px;flex:none}
.foot-line{left:0;top:337px;width:1200px;height:1px;background:var(--grey-line)}
.copyright{top:366px;width:100%;font-size:11px;color:var(--ink)}
</style>
</head>
<body>

<header class="section site-header">
  <div class="abs brand"><span class="brand-mark"></span><span class="brand-name">KELVANBROOK</span></div>
  <div class="abs brand-tagline">Reliable technology care for your team… every day, every time</div>
  <div class="abs callbar">
    <span class="round-icon"><svg width="14" height="14" viewBox="0 0 24 24"><path fill="#fff" d="M6.6 10.8a15.1 15.1 0 0 0 6.6 6.6l2.2-2.2c.3-.3.7-.4 1-.2 1.1.4 2.3.6 3.6.6.6 0 1 .4 1 1V20c0 .6-.4 1-1 1A17 17 0 0 1 3 4c0-.6.4-1 1-1h3.5c.6 0 1 .4 1 1 0 1.3.2 2.5.6 3.6.1.3 0 .7-.2 1z"/></svg></span>
    <span>Call us :</span><span class="phone">(555).014.2290</span>
    <span>Follow us :</span>
    <span class="social"><span class="s1"></span><span class="s2"></span><span class="s3"></span></span>
  </div>
  <nav class="abs main-nav">
    <a class="active">Home</a><a>About Us</a><a>Services</a><a>Support</a><a>Clients</a><a>Careers</a><a>Contact Us</a>
  </nav>
</header>

<section class="section hero">
  <div class="hero-photo" role="img" aria-label="Photo of a businesswoman working on a laptop in a bright office"></div>
  <div class="abs hero-box">
    <h1 class="hero-title">IT Solutions<br>That Work For<br>Your Business</h1>
    <div class="hero-sub">A Full Service Technology Company</div>
  </div>
  <div class="abs dots"><span></span><span class="on"></span><span></span><span></span><span></span></div>
</section>

<section class="section support">
  <h2 class="abs heading center">IT Support Solutions</h2>
  <div class="rule"></div>
  <div class="abs support-item" style="left:108px">
    <svg width="54" height="54" viewBox="0 0 54 54" fill="none" stroke="#f08a24" stroke-width="3"><circle cx="27" cy="10" r="6" fill="#f08a24"/><path d="M27 18v10M10 28h34M10 28v8M27 28v8M44 28v8"/><circle cx="10" cy="41" r="4" fill="#f08a24"/><circle cx="27" cy="41" r="4" fill="#f08a24"/><circle cx="44" cy="41" r="4" fill="#f08a24"/><path d="M4 52c0-4 3-6 6-6s6 2 6 6M21 52c0-4 3-6 6-6s6 2 6 6M38 52c0-4 3-6 6-6s6 2 6 6"/></svg>
    <div class="a">Network</div><div class="b">Administration</div></div>
  <div class="abs support-item" style="left:289px">
    <svg width="54" height="54" viewBox="0 0 54 54" fill="none" stroke="#f08a24" stroke-width="3"><path d="M10 30v-6a17 17 0 0 1 34 0v6"/><rect x="6" y="28" width="9" height="14" rx="3" fill="#f08a24"/><rect x="39" y="28" width="9" height="14" rx="3" fill="#f08a24"/><path d="M44 42c0 6-6 8-14 8"/><circle cx="28" cy="50" r="3" fill="#f08a24"/></svg>
    <div class="a">Desktop</div><div class="b">Support</div></div>
  <div class="abs support-item" style="left:457px">
    <svg width="54" height="54" viewBox="0 0 54 54" fill="none" stroke="#f08a24" stroke-width="3"><path d="M22 4v8M32 4v8"/><rect x="18" y="12" width="18" height="14" rx="3" fill="#f08a24"/><path d="M27 26v10c0 8-8 6-8 12v4"/></svg>
    <div class="a">Network</div><div class="b">Cabling</div></div>
  <div class="abs support-item" style="left:624px">
    <svg width="54" height="54" viewBox="0 0 54 54" fill="none" stroke="#f08a24" stroke-width="3.5" stroke-linecap="round"><path d="M5 20a31 31 0 0 1 44 0M12 28a21 21 0 0 1 30 0M19 36a11 11 0 0 1 16 0"/><circle cx="27" cy="44" r="3.5" fill="#f08a24"/></svg>
    <div class="a">Wireless</div><div class="b">Networks</div></div>
  <div class="abs support-item" style="left:801px">
    <svg width="54" height="54" viewBox="0 0 54 54"><path d="M27 4l19 7v14c0 13-8 22-19 26C16 47 8 38 8 25V11z" fill="#f08a24"/><path d="M27 12l11 4v9c0 8-5 14-11 17z" fill="#fff" opacity=".6"/></svg>
    <div class="a">Antivirus</div><div class="b">Solutions</div></div>
  <div class="abs support-item" style="left:957px">
    <svg width="54" height="54" viewBox="0 0 54 54" fill="none" stroke="#f08a24" stroke-width="3"><path d="M27 4l20 12v22L27 50 7 38V16z"/><rect x="19" y="25" width="16" height="12" rx="2" fill="#f08a24"/><path d="M22 25v-4a5 5 0 0 1 10 0v4"/></svg>
    <div class="a">Network</div><div class="b">Security</div></div>
</section>

<section class="section welcome">
  <h2 class="abs heading center">Welcome To</h2>
  <div class="abs big-name center">KELVANBROOK</div>
  <p class="abs center">Outsourcing is subcontracting a process, such as product design or manufacturing, to a third-party company.[1] The decision to outsource is often made in the interest of lowering firm costs, redirecting or conserving energy directed at the competencies of a particular business, or to make more efficient use of land, labor, capital, (information) technology and resources</p>
  <div class="abs btn">Read More</div>
</section>

<section class="section services">
  <div class="abs service" style="left:85px">
    <div class="ring"><div class="disc"><svg width="52" height="52" viewBox="0 0 52 52" fill="none" stroke="#fff" stroke-width="3"><circle cx="20" cy="22" r="9"/><circle cx="20" cy="22" r="3"/><path d="M20 8v5M20 31v5M6 22h5M29 22h5M10 12l3 3M27 29l3 3M10 32l3-3M27 15l3-3"/><circle cx="37" cy="38" r="5"/><path d="M37 29v3M37 44v3M28 38h3M43 38h3"/></svg></div></div>
    <h3>Managed IT<br><span>Solutions</span></h3>
    <p>Our staff will design, service, administer and maintain your IT needs. We are well versed on all major operating system, and network appliances</p>
  </div>
  <div class="abs service" style="left:435px">
    <div class="ring"><div class="disc"><svg width="52" height="52" viewBox="0 0 52 52" fill="none" stroke="#fff" stroke-width="3"><circle cx="26" cy="20" r="9" fill="#fff"/><path d="M14 20a12 12 0 0 1 24 0"/><rect x="11" y="18" width="5" height="9" rx="2" fill="#fff"/><rect x="36" y="18" width="5" height="9" rx="2" fill="#fff"/><path d="M12 48c0-9 6-14 14-14s14 5 14 14z" fill="#fff"/></svg></div></div>
    <h3>Remote Diagnostic<br><span>And Support</span></h3>
    <p>Do you need a quick solution to a technical problem? With our live remote-assistance tool, a member of our support team can view your desktop and share control of your mouse and keyboard to get you on your way to a solution.</p>
  </div>
  <div class="abs service" style="left:795px">
    <div class="ring"><div class="disc"><svg width="52" height="52" viewBox="0 0 52 52" fill="none" stroke="#fff" stroke-width="2.5"><circle cx="26" cy="26" r="11"/><ellipse cx="26" cy="26" rx="5" ry="11"/><path d="M15 26h22M26 4v11M26 37v11M4 26h11M37 26h11"/><circle cx="26" cy="4" r="2.5" fill="#fff"/><circle cx="26" cy="48" r="2.5" fill="#fff"/><circle cx="4" cy="26" r="2.5" fill="#fff"/><circle cx="48" cy="26" r="2.5" fill="#fff"/></svg></div></div>
    <h3>IT Infrastructure Design<br><span>And Installation</span></h3>
    <p>Do you have more than one site? Do you need remote access? We can design and implement LANS/WANS and VPN's. Make your important data available to you wherever you are.</p>
  </div>
</section>

<section class="section flexible">
  <h2 class="abs heading">Flexible Solutions For Your<br>Business Needs</h2>
  <p class="abs">Kelvanbrook is a technology solution provider based in Greenfield, Ohio. Our goal is to make technology a non-issue for individuals and small to medium size businesses ranging from 5 to 150 Users. Kelvanbrook has the experience, the tools, high-level technology solutions and training to power your business and your work force. We understand that all business's have one goal in common!</p>
  <div class="abs divider"></div>
  <div class="abs flex-mark"><div class="sq"></div></div>
  <div class="abs feature" style="left:132px"><svg width="30" height="22" viewBox="0 0 30 22" fill="none" stroke="#f08a24" stroke-width="2"><circle cx="15" cy="11" r="3" fill="#f08a24"/><path d="M9 5a8 8 0 0 0 0 12M21 5a8 8 0 0 1 0 12M5 1a14 14 0 0 0 0 20M25 1a14 14 0 0 1 0 20"/></svg>Telecommunications</div>
  <div class="abs feature" style="left:369px"><svg width="26" height="24" viewBox="0 0 26 24"><rect x="2" y="8" width="22" height="15" rx="2" fill="#f08a24"/><path d="M8 8l5-6 5 6" fill="none" stroke="#f08a24" stroke-width="2"/></svg>Disaster Recovery</div>
  <div class="abs feature" style="left:606px"><svg width="26" height="24" viewBox="0 0 26 24" fill="#f08a24"><rect x="2" y="14" width="3" height="8"/><rect x="7" y="6" width="3" height="16"/><rect x="12" y="10" width="3" height="12"/><rect x="17" y="2" width="3" height="20"/><rect x="22" y="12" width="3" height="10"/></svg>Audio/Video Multimedia</div>
  <div class="abs feature" style="left:843px"><svg width="28" height="24" viewBox="0 0 28 24" fill="none" stroke="#f08a24" stroke-width="2"><rect x="2" y="2" width="24" height="15" rx="1"/><path d="M10 22h8M14 17v5"/><circle cx="14" cy="9.5" r="3" fill="#f08a24"/></svg>Web Design</div>
</section>

<section class="section testimonials">
  <h2 class="abs heading center">Testimonials</h2>
  <div class="rule"></div>
  <div class="abs arrow" style="left:286px;top:194px">‹</div>
  <div class="abs arrow" style="left:882px;top:194px">›</div>
  <div class="abs avatar" role="img" aria-label="Client portrait" style="left:348px;top:185px;width:64px;height:64px;opacity:.7"></div>
  <div class="abs avatar" role="img" aria-label="Client portrait" style="left:433px;top:177px;width:80px;height:80px"></div>
  <div class="abs avatar main" role="img" aria-label="Featured client portrait" style="left:530px;top:147px;width:140px;height:140px"></div>
  <div class="abs avatar" role="img" aria-label="Client portrait" style="left:685px;top:177px;width:80px;height:80px"></div>
  <div class="abs avatar" role="img" aria-label="Client portrait" style="left:788px;top:185px;width:64px;height:64px;opacity:.7"></div>
  <div class="abs quote-mark" style="left:268px;top:292px">“</div>
  <div class="abs quote-mark" style="left:832px;top:372px">”</div>
  <p class="abs">There are many variations of passages of Lorem Ipsum available, but the majority have suffered alteration in some form, by injected humour, or randomised words which don't look even slightly believable. If you are going to use a passage of Lorem Ipsum.</p>
  <div class="abs btn name-tag"><b>Martin Okafor,</b> <span>Leeds</span></div>
</section>

<footer class="section site-footer">
  <div class="abs brand"><span class="brand-mark"></span><span class="brand-name">KELVANBROOK</span></div>
  <div class="abs brand-tagline">Reliable technology care for your team… every day, every time</div>
  <div class="abs heading connect center">Connect With Us</div>
  <div class="abs foot-social"><span class="s1"></span><span class="s2"></span><span class="s3"></span></div>

  <div class="abs menu">
    <div class="heading foot-title">Menu</div>
    <ul><li>Home</li><li>About Us</li><li>Services</li><li>Support</li><li>Clients</li><li>Careers</li><li>Contact us</li></ul>
  </div>

  <div class="abs contact">
    <div class="heading foot-title">Contact Us</div>
    <div class="contact-row" style="top:44px"><span class="round-icon"><svg width="12" height="16" viewBox="0 0 12 16"><path fill="#fff" d="M6 0a6 6 0 0 0-6 6c0 4.5 6 10 6 10s6-5.5 6-10a6 6 0 0 0-6-6zm0 8.5A2.5 2.5 0 1 1 6 3.5a2.5 2.5 0 0 1 0 5z"/></svg></span><span>418 Larchmont Road<br>Suite 210, Greenfield, Ohio 45123</span></div>
    <div class="contact-row" style="top:116px"><span class="round-icon"><svg width="13" height="13" viewBox="0 0 24 24"><path fill="#fff" d="M6.6 10.8a15.1 15.1 0 0 0 6.6 6.6l2.2-2.2c.3-.3.7-.4 1-.2 1.1.4 2.3.6 3.6.6.6 0 1 .4 1 1V20c0 .6-.4 1-1 1A17 17 0 0 1 3 4c0-.6.4-1 1-1h3.5c.6 0 1 .4 1 1 0 1.3.2 2.5.6 3.6.1.3 0 .7-.2 1z"/></svg></span><span>(555).014.2290</span></div>
    <div class="contact-row" style="top:163px"><span class="round-icon"><svg width="14" height="10" viewBox="0 0 14 10"><rect width="14" height="10" rx="1" fill="#fff"/><path d="M1 1l6 5 6-5" fill="none" stroke="#f08a24" stroke-width="1.3"/></svg></span><span>info@kelvanbrook.com</span></div>
  </div>

  <div class="abs foot-line"></div>
  <div class="abs copyright center">Copyrights © 2017 All Rights Reserved</div>
</footer>

</body>
</html>
```